Marlowe Group needs a business card

I would like the card to be simple but modern and elegant.
I like black and white.
or black and gold.
we are a private finance lender and also are involved in property and property developments.

please look at the business card photos i provided i would like M.G only one one side and all the other details on the other side use fonts that tie in with my theme.

Industry/Entity Type

Finance

Contact Information for Business Card

Marlowe Group (M.G) Daniel Marlowe M: 0413586207 E: danmarl@inboxmail.test

Font styles to use
Other font styles liked:
• Use fonts that would reflect our business

Colors
000000
ffffff

Requirements
Must have
• one side of details
• other side has either M.G or Marlowe Group like in the photos provided

```html
<!DOCTYPE html>
<html lang="en">
<head>
<meta charset="UTF-8">
<title>Marlowe Group — Business Card</title>
<link rel="stylesheet" href="https://fonts.googleapis.com/css2?family=Source+Sans+3:ital,wght@0,400;0,600;1,400&display=swap">
<style>
  :root {
    --backdrop: #dcdad6;
    --frost-top: #f1f0ee;
    --frost-bottom: #dedcd9;
    --band-dark: #060606;
    --band-mid: #1c1c1c;
    --divider: #8a8a8a;
    --mark-ink: #0a0a0a;
    --name-ink: #dccbb2;
    --contact-ink: #cdbcaa;
    --web-ink: #8f7e77;
  }

  * { margin: 0; padding: 0; box-sizing: border-box; }

  html, body {
    width: 1200px;
    height: 969px;
    overflow: hidden;
    background: var(--backdrop);
    font-family: "Source Sans 3", "Myriad Pro", Arial, sans-serif;
  }

  .card {
    position: absolute;
    left: 164px;
    top: 245px;
    width: 872px;
    height: 495px;
    border-radius: 22px;
    overflow: hidden;
    background: linear-gradient(180deg, var(--frost-top), var(--frost-bottom));
    box-shadow: 0 18px 40px rgba(0, 0, 0, 0.18);
  }

  .card__brand-area {
    position: absolute;
    left: 0;
    top: 0;
    width: 100%;
    height: 274px;
    display: flex;
    align-items: center;
    justify-content: center;
  }

  .card__brand {
    font-weight: 600;
    font-size: 66px;
    line-height: 1;
    color: var(--mark-ink);
    margin-top: 20px;
  }

  .card__divider {
    position: absolute;
    left: 0;
    top: 274px;
    width: 100%;
    height: 4px;
    background: var(--divider);
  }

  .card__details {
    position: absolute;
    left: 0;
    top: 278px;
    width: 100%;
    height: 217px;
    background: linear-gradient(180deg, var(--band-mid) 0%, var(--band-dark) 30%, var(--band-dark) 100%);
    text-align: center;
    padding-top: 44px;
  }

  .card__name {
    font-weight: 600;
    font-size: 30px;
    letter-spacing: 0.5px;
    color: var(--name-ink);
  }

  .card__contact {
    margin-top: 16px;
    font-size: 23px;
    color: var(--contact-ink);
  }

  .card__contact-sep { padding: 0 4px; }

  .card__web {
    margin-top: 4px;
    font-size: 23px;
    font-style: italic;
    letter-spacing: 0.5px;
    color: var(--web-ink);
  }
</style>
</head>
<body>
  <div class="card">
    <div class="card__brand-area">
      <div class="card__brand">Marlowe Group</div>
    </div>
    <div class="card__divider"></div>
    <div class="card__details">
      <div class="card__name">Daniel Marlowe</div>
      <div class="card__contact">0413586207<span class="card__contact-sep">|</span>danmarl@inboxmail.test</div>
      <div class="card__web">www.marlowegroup.test</div>
    </div>
  </div>
</body>
</html>
```